Dietitian needs awesome business card

I need a contemporary design that's eye catching but professional.
My card is to given to doctors, specialists and patients alike.
I manage patients with chronic diseases
I have uploaded my logo and current business card, I would also like the other Certified Clinical Nutritionist logo incorporated into the design

Target Market(s)

Doctors, specialists and patients

Industry/Entity Type

Healthcare

Contact Information for Business Card

www.brightfieldnutrition.com.au
Ph: 0427 561 903
Fax: 6457 2183
email: marcus.k.diet@fernmail.com
Space on the back of the card with: Appointment date, Appointment time and appointment location

Font styles to use
Serif

Colors
fbee3e
876aae
ffc214

Requirements
Must have
• My Logo
• Certified Clinical Nutritionist Logo
• My 4 locations - Pinebrook Medical Centre, North Corrin Health, Hollis Medical, Ashcombe Doctors Surgery
Nice to have
• I like the colours in my current business card

```html
<!DOCTYPE html>
<html lang="en">
<head>
<meta charset="utf-8">
<title>Brightfield Nutrition &amp; Dietetics – Business Card</title>
<link rel="stylesheet" href="https://fonts.googleapis.com/css2?family=Philosopher&family=Gentium+Book+Plus&family=Open+Sans:wght@400&display=swap">
<style>
  :root {
    --bg: #e6e7e8;
    --card: #ffffff;
    --navy: #1f2f8c;
    --blue: #0a7fcf;
    --deep-navy: #1b1f78;
    --green: #7cc22a;
    --lime: #b5d80c;
    --text: #4a4a4a;
    --orange: #f47b20;
  }
  * { margin: 0; padding: 0; box-sizing: border-box; }
  html, body { width: 1105px; height: 1200px; overflow: hidden; }
  body {
    background: var(--bg);
    position: relative;
    font-family: "Open Sans", sans-serif;
  }
  .card {
    position: absolute;
    left: 172px;
    width: 760px;
    height: 435px;
    background: var(--card);
    overflow: hidden;
    box-shadow: 0 2px 6px rgba(0,0,0,0.12);
  }
  .card--front { top: 120px; }
  .card--back { top: 650px; }

  /* Front */
  .brand {
    position: absolute; left: 46px; top: 58px;
    display: flex; align-items: center; gap: 16px;
  }
  .brand__dot {
    width: 74px; height: 74px; border-radius: 50%;
    background: var(--green);
  }
  .brand__name {
    font-family: "Philosopher", sans-serif;
    color: var(--navy);
    font-size: 36px; line-height: 1.05;
  }
  .person { position: absolute; left: 46px; top: 222px; }
  .person__name {
    font-family: "Philosopher", sans-serif;
    font-size: 28px; color: var(--navy);
  }
  .person__role {
    font-family: "Philosopher", sans-serif;
    font-size: 21px; color: var(--green); margin-top: 4px;
  }
  .contact {
    position: absolute; left: 390px; top: 228px;
    list-style: none;
    font-family: "Gentium Book Plus", serif;
    font-size: 20px; color: var(--text);
  }
  .contact li { display: flex; align-items: center; gap: 12px; height: 29.5px; }
  .contact svg { width: 18px; height: 18px; fill: var(--navy); flex: none; }
  .stripe { position: absolute; top: 405px; height: 27px; }
  .stripe--green { left: 0; width: 198px; background: linear-gradient(90deg, var(--green), var(--lime)); }
  .stripe--blue { left: 204px; right: 0; background: linear-gradient(90deg, var(--deep-navy), var(--blue) 55%, var(--deep-navy)); }

  /* Back */
  .backdrop {
    position: absolute; left: -60px; top: 60px;
    width: 380px; height: 380px; border-radius: 50%;
    background: radial-gradient(circle at 35% 40%, #e3ebf8 0%, #eef4e2 60%, #ffffff 100%);
    opacity: 0.9;
  }
  .cert-badge {
    position: absolute; left: 389px; top: 50px;
    width: 181px; height: 84px; background: var(--orange);
  }
  .cert-badge__seal {
    position: absolute; right: 14px; top: 11px;
    width: 62px; height: 62px; border-radius: 50%; background: #fff;
  }
  .appt {
    position: absolute; left: 389px;
    font-size: 20px; color: var(--navy);
  }
  .appt--date { top: 180px; }
  .appt--time { top: 228px; }
  .appt__line { letter-spacing: 1px; font-size: 15px; }
  .appt__ampm { font-size: 15px; margin-left: 6px; }
  .locations {
    position: absolute; left: 389px; top: 288px;
    list-style: none; font-size: 19px; color: var(--text);
  }
  .locations li { display: flex; align-items: center; gap: 14px; height: 27.5px; }
  .locations .box { width: 15px; height: 15px; border: 1.5px solid var(--navy); flex: none; }
</style>
</head>
<body>

<section class="card card--front">
  <div class="brand">
    <span class="brand__dot"></span>
    <span class="brand__name">Brightfield<br>Nutrition &amp; Dietetics</span>
  </div>

  <div class="person">
    <div class="person__name">Marcus Kellaway</div>
    <div class="person__role">Nutritionist &amp; Chef</div>
  </div>

  <ul class="contact">
    <li><svg viewBox="0 0 24 24"><path d="M6.6 10.8a15.1 15.1 0 0 0 6.6 6.6l2.2-2.2c.3-.3.7-.4 1-.2 1.1.4 2.3.6 3.6.6.6 0 1 .4 1 1V20c0 .6-.4 1-1 1A17 17 0 0 1 3 4c0-.6.4-1 1-1h3.5c.6 0 1 .4 1 1 0 1.3.2 2.5.6 3.6.1.3 0 .7-.2 1z"/></svg>0427 561 903</li>
    <li><svg viewBox="0 0 24 24"><path d="M6 2h9l3 3v4H6z M3 10h18v8H3z M6 15h12v7H6z"/></svg>6457 2183</li>
    <li><svg viewBox="0 0 24 24"><path d="M2 5h20v14H2z" /><path d="M2 5l10 8 10-8" fill="none" stroke="#fff" stroke-width="2"/></svg>marcus.k.diet@fernmail.com</li>
    <li><svg viewBox="0 0 24 24"><circle cx="12" cy="12" r="10"/><path d="M7 8c2 0 3 1 3 3s-2 2-2 4M15 5c-1 2 1 3 2 4s2 3 0 5" fill="none" stroke="#fff" stroke-width="1.6"/></svg>brightfieldnutrition.com.au</li>
  </ul>

  <div class="stripe stripe--green"></div>
  <div class="stripe stripe--blue"></div>
</section>

<section class="card card--back">
  <div class="backdrop" role="img" aria-label="Faint brand symbol watermark"></div>

  <div class="cert-badge" role="img" aria-label="Certification badge">
    <span class="cert-badge__seal"></span>
  </div>

  <div class="appt appt--date">Date : <span class="appt__line">.......................................</span></div>
  <div class="appt appt--time">Time : <span class="appt__line">............................</span><span class="appt__ampm">AM/PM</span></div>

  <ul class="locations">
    <li><span class="box"></span>Pinebrook Medical Centre</li>
    <li><span class="box"></span>North Corrin Health</li>
    <li><span class="box"></span>Hollis Medical</li>
    <li><span class="box"></span>Ashcombe Doctors Surgery</li>
  </ul>
</section>

</body>
</html>
```